Corvel Capital LLC

Need Professional Business cards for New Investment Fund

Target Market(s)

High Quality investors

Industry/Entity Type

Financial

Contact Information for Business Card

Phone Number +1 555 284 6190
Name Lukas Varenko
Title Fund Manager
email lv@FundCorvel.com
Website www.FundCorvel.com

Colors

Designer to choose colors to be used in the design.

Requirements
Must have
• Must have our Logo and all of the above. Must be made so lettering and loge can be raised

```html
<!DOCTYPE html>
<html lang="en">
<head>
<meta charset="utf-8">
<title>Corvel Capital LLC — Business Cards</title>
<link rel="stylesheet" href="https://fonts.googleapis.com/css2?family=Open+Sans:wght@400;600&display=swap">
<style>
  :root {
    --backdrop: #d5d5d5;
    --card-white: #ffffff;
    --deep-green: #3f4a40;
    --mid-green: #5a6b5b;
    --accent-green: #4cb74a;
    --text-grey: #555a55;
    --logo-grey: #4a4f4a;
  }
  * { margin: 0; padding: 0; box-sizing: border-box; }
  html, body {
    width: 1200px;
    height: 900px;
    overflow: hidden;
    background: var(--backdrop);
    font-family: "Open Sans", sans-serif;
  }
  .stage {
    position: relative;
    width: 1200px;
    height: 900px;
  }
  .card {
    position: absolute;
    width: 520px;
    height: 300px;
    box-shadow: 0 6px 14px rgba(0,0,0,0.18);
  }
  .card--back {
    left: 50px;
    top: 190px;
    background: linear-gradient(135deg, var(--deep-green) 0%, var(--mid-green) 45%, #4f8a4e 75%, var(--deep-green) 100%);
  }
  .card--front {
    left: 630px;
    top: 410px;
    background: var(--card-white);
  }
  .brand {
    position: absolute;
    left: 40px;
    bottom: 50px;
    display: flex;
    align-items: center;
    gap: 10px;
  }
  .brand__dot {
    width: 22px;
    height: 22px;
    border-radius: 50%;
    background: var(--accent-green);
  }
  .brand__name {
    font-size: 24px;
    font-weight: 600;
    color: var(--logo-grey);
    white-space: nowrap;
  }
  .contact {
    position: absolute;
    left: 270px;
    top: 62px;
  }
  .contact__name {
    font-size: 19px;
    font-weight: 600;
    color: var(--accent-green);
    line-height: 1.2;
  }
  .contact__title {
    font-size: 14px;
    color: var(--text-grey);
    margin-bottom: 18px;
  }
  .contact__list { list-style: none; }
  .contact__item {
    display: flex;
    align-items: center;
    gap: 8px;
    font-size: 14px;
    color: var(--text-grey);
    line-height: 1.55;
    white-space: nowrap;
  }
  .contact__icon {
    width: 12px;
    height: 12px;
    flex: none;
  }
</style>
</head>
<body>
  <main class="stage">
    <section class="card card--back" role="img" aria-label="Card back: repeated decorative pattern in green and grey on a dark green ground"></section>

    <section class="card card--front">
      <div class="contact">
        <p class="contact__name">Lukas Varenko</p>
        <p class="contact__title">Fund Manager</p>
        <ul class="contact__list">
          <li class="contact__item">
            <svg class="contact__icon" viewBox="0 0 12 12" aria-hidden="true"><path d="M2.5 1 L4.5 1 L5 3.5 L3.8 4.4 C4.5 6 6 7.5 7.6 8.2 L8.5 7 L11 7.5 L11 9.5 C11 10.3 10.3 11 9.5 11 C5 11 1 7 1 2.5 C1 1.7 1.7 1 2.5 1 Z" fill="var(--accent-green)"/></svg>
            +1 555 284 6190
          </li>
          <li class="contact__item">
            <svg class="contact__icon" viewBox="0 0 12 12" aria-hidden="true"><rect x="0.75" y="2.25" width="10.5" height="7.5" fill="none" stroke="var(--accent-green)" stroke-width="1.5"/><path d="M1 2.5 L6 6.5 L11 2.5" fill="none" stroke="var(--accent-green)" stroke-width="1.3"/></svg>
            lv@FundCorvel.com
          </li>
          <li class="contact__item">
            <svg class="contact__icon" viewBox="0 0 12 12" aria-hidden="true"><circle cx="6" cy="6" r="5.2" fill="none" stroke="var(--accent-green)" stroke-width="1.3"/><ellipse cx="6" cy="6" rx="2.2" ry="5.2" fill="none" stroke="var(--accent-green)" stroke-width="1"/><line x1="0.8" y1="6" x2="11.2" y2="6" stroke="var(--accent-green)" stroke-width="1"/></svg>
            www.FundCorvel.com
          </li>
        </ul>
      </div>

      <div class="brand">
        <span class="brand__dot" aria-hidden="true"></span>
        <span class="brand__name">Corvel Capital</span>
      </div>
    </section>
  </main>
</body>
</html>
```